Brightfen Business Card Redesign & Logo Update

We need to update our business cards to something more modern and fresh. Brightfen can provide the current color schemes and old design examples, but welcome creativity in helping us with this redesign. PLEASE NOTE that we no longer utilize the "tree" and/or "leaf" imagery in our branding. If able would apprecaite an update on the quality of our "words only" logo in Ai. / PNG formats too.

Target Market(s)

Investors, landowners, corporate partners, contractors

Industry/Entity Type

Environmental Restoration & Conservation

Contact Information for Business Card

Logo, persons name, title, mailing address, phone and email, website url

Font styles to use
Other font styles liked:
• Merriweather

Requirements
Nice to have
• Logo, persons name, title, mailing address, phone and email, website url, but open to ideams
Should not have
• No all back backgrounds

```html
<!DOCTYPE html>
<html lang="en">
<head>
<meta charset="utf-8">
<title>Brightfen Business Card</title>
<link rel="stylesheet" href="https://fonts.googleapis.com/css2?family=Oswald:wght@500;700&family=Merriweather:wght@400;700&display=swap">
<style>
  :root {
    --backdrop: #9e9e9e;
    --card: #ffffff;
    --green: #1a7a3e;
    --orange: #ee7d22;
    --ink: #1c1c1c;
    --text: #222222;
    --band-text: #ffffff;
  }
  * { box-sizing: border-box; margin: 0; padding: 0; }
  html, body {
    width: 1146px;
    height: 1200px;
    overflow: hidden;
    background: var(--backdrop);
  }
  .canvas {
    position: relative;
    width: 1146px;
    height: 1200px;
  }
  .card {
    position: absolute;
    left: 176px;
    width: 797px;
    background: var(--card);
  }
  .card--front { top: 113px; height: 455px; }
  .card--back  { top: 594px; height: 467px; }

  .brand {
    position: absolute;
    left: 0;
    right: 0;
    text-align: center;
  }
  .brand__name {
    font-family: "Oswald", sans-serif;
    font-weight: 700;
    color: var(--green);
    line-height: 1;
    letter-spacing: 1px;
  }
  .brand__tagline {
    font-family: "Oswald", sans-serif;
    font-weight: 500;
    color: var(--ink);
    line-height: 1;
    letter-spacing: 0.3px;
  }
  .card--front .brand { top: 168px; }
  .card--front .brand__name { font-size: 86px; }
  .card--front .brand__tagline { font-size: 21px; margin-top: 8px; }

  .card--back .brand { top: 98px; }
  .card--back .brand__name { font-size: 74px; }
  .card--back .brand__tagline { font-size: 19px; margin-top: 6px; }

  .person {
    position: absolute;
    right: 434px;
    top: 287px;
    text-align: right;
    font-family: "Merriweather", serif;
  }
  .person__name {
    font-size: 25px;
    font-weight: 700;
    line-height: 1.2;
    text-transform: uppercase;
  }
  .person__first { color: var(--orange); }
  .person__last { color: var(--green); }
  .person__title {
    font-size: 20px;
    color: var(--text);
    margin-top: 6px;
  }
  .divider {
    position: absolute;
    left: 384px;
    top: 271px;
    width: 2px;
    height: 99px;
    background: var(--green);
  }
  .contacts {
    position: absolute;
    left: 400px;
    top: 274px;
    list-style: none;
    font-family: "Merriweather", serif;
    font-size: 21px;
    color: var(--text);
  }
  .contacts__item {
    display: flex;
    align-items: center;
    height: 29px;
  }
  .contacts__icon {
    width: 17px;
    height: 17px;
    margin-right: 9px;
    fill: var(--green);
    flex: none;
  }
  .address-band {
    position: absolute;
    left: 0;
    right: 0;
    top: 409px;
    height: 41px;
    background: var(--green);
    color: var(--band-text);
    font-family: "Merriweather", serif;
    font-size: 20px;
    line-height: 41px;
    text-align: center;
  }
</style>
</head>
<body>
<main class="canvas">

  <section class="card card--front" aria-label="Business card front">
    <div class="brand">
      <div class="brand__name">BRIGHTFEN</div>
      <div class="brand__tagline">ENVIRONMENTAL CREDIT COMPANY</div>
    </div>
  </section>

  <section class="card card--back" aria-label="Business card back">
    <div class="brand">
      <div class="brand__name">BRIGHTFEN</div>
      <div class="brand__tagline">ENVIRONMENTAL CREDIT COMPANY</div>
    </div>

    <div class="person">
      <div class="person__name"><span class="person__first">Maren</span> <span class="person__last">Holt</span></div>
      <div class="person__title">Founder</div>
    </div>

    <div class="divider"></div>

    <ul class="contacts">
      <li class="contacts__item">
        <svg class="contacts__icon" viewBox="0 0 24 24" aria-hidden="true"><path d="M6.6 10.8a15.1 15.1 0 0 0 6.6 6.6l2.2-2.2a1 1 0 0 1 1-.25 11.4 11.4 0 0 0 3.6.57 1 1 0 0 1 1 1V20a1 1 0 0 1-1 1A17 17 0 0 1 3 4a1 1 0 0 1 1-1h3.5a1 1 0 0 1 1 1c0 1.25.2 2.45.57 3.6a1 1 0 0 1-.25 1z"/></svg>
        <span>(555) 214-3390</span>
      </li>
      <li class="contacts__item">
        <svg class="contacts__icon" viewBox="0 0 24 24" aria-hidden="true"><path d="M3 5h18a1 1 0 0 1 1 1v.4l-10 6.2L2 6.4V6a1 1 0 0 1 1-1zm-1 3.7 10 6.2 10-6.2V18a1 1 0 0 1-1 1H3a1 1 0 0 1-1-1z"/></svg>
        <span>hello@brightfen.com</span>
      </li>
      <li class="contacts__item">
        <svg class="contacts__icon" viewBox="0 0 24 24" aria-hidden="true"><path d="M12 2a10 10 0 1 0 0 20 10 10 0 0 0 0-20zm6.9 6h-3a15.6 15.6 0 0 0-1.4-3.6A8 8 0 0 1 18.9 8zM12 4c.8 1.2 1.5 2.5 1.9 4h-3.8c.4-1.5 1.1-2.8 1.9-4zM4.3 14a8.2 8.2 0 0 1 0-4h3.4a16.5 16.5 0 0 0 0 4zm.8 2h3a15.6 15.6 0 0 0 1.4 3.6A8 8 0 0 1 5.1 16zm3-8h-3a8 8 0 0 1 4.4-3.6A15.6 15.6 0 0 0 8.1 8zM12 20c-.8-1.2-1.5-2.5-1.9-4h3.8c-.4 1.5-1.1 2.8-1.9 4zm2.3-6H9.7a14.7 14.7 0 0 1 0-4h4.6a14.7 14.7 0 0 1 0 4zm.2 5.6a15.6 15.6 0 0 0 1.4-3.6h3a8 8 0 0 1-4.4 3.6zm1.8-5.6a16.5 16.5 0 0 0 0-4h3.4a8.2 8.2 0 0 1 0 4z"/></svg>
        <span>www.brightfen.com</span>
      </li>
    </ul>

    <div class="address-band">48 Marsh Lane, Suite 12, Fenwick, OR 97402</div>
  </section>

</main>
</body>
</html>
```